Letter and Envelope Design For Harborline Realty

Please design a letter and an envelope incorporating our logo (See Attached). We are also launched a business card contest. Since we want them to match, please feel free to submit a design for both the business card and also the letter design and envelope.

Requirements
Must have
• The envelope, the letter and the business cards must match somehow connecting the designs. We want them to have something that holds them together besides the logo.

```html
<!DOCTYPE html>
<html lang="en">
<head>
<meta charset="utf-8">
<title>Harborline Realty – Letter and Envelope</title>
<link rel="stylesheet" href="https://fonts.googleapis.com/css2?family=Josefin+Sans:wght@600&family=Roboto:wght@400;500&display=swap">
<style>
:root{
  --backdrop:#686868;
  --paper:#f7f7f5;
  --brand-blue:#0b1a8c;
  --brand-grey:#5b5b5b;
  --ink:#6e6e6e;
  --ink-dark:#3d3d3d;
  --watermark:#e9e9e7;
}
*{margin:0;padding:0;box-sizing:border-box}
html,body{width:1200px;height:816px;overflow:hidden;background:var(--backdrop)}
body{position:relative;font-family:"Roboto",Arial,sans-serif}
.sheet{position:absolute;background:var(--paper);overflow:hidden}
.wave{position:absolute;left:0;bottom:0;display:block}

/* brand lockup */
.brand{position:absolute;text-align:center;color:var(--brand-blue);font-family:"Josefin Sans",Arial,sans-serif;font-weight:600;line-height:1}
.brand-ring{display:block;margin:0 auto 8px;width:42px;height:42px;border:2px solid var(--brand-blue);border-radius:50%}
.brand-name{display:block;font-size:13px;letter-spacing:1.6px}
.brand-sub{display:block;font-size:9px;letter-spacing:3.2px;margin-top:3px}

/* contact block */
.contact{position:absolute;font-size:7.2px;font-weight:400;color:var(--ink-dark);line-height:9.4px}
.contact-row{display:flex;align-items:center;gap:4px;white-space:nowrap}
.contact-row svg{width:7px;height:7px;fill:var(--brand-blue);flex:none}
.contact-gap{width:6px}
.contact-indent{padding-left:11px}
.site{position:absolute;color:#fff;font-size:7.2px;font-weight:400;white-space:nowrap;z-index:1}

/* envelope front */
.envelope-front{left:140px;top:221px;width:474px;height:213px}
.envelope-front .brand{left:20px;top:24px;width:116px}
.envelope-front .contact{left:24px;top:133px}
.envelope-front .site{left:349px;top:190px}

/* envelope back */
.envelope-back{left:140px;top:456px;width:474px;height:213px}
.flap{position:absolute;left:0;top:0}
.flap-ring{position:absolute;left:208px;top:9px;width:58px;height:58px;border:1px solid rgba(255,255,255,.12);border-radius:50%}
.envelope-back .brand{left:137px;top:27px;width:200px;color:#fff}
.envelope-back .brand-name{font-size:12.5px}
.envelope-back .brand-sub{font-size:8.5px}

/* letterhead */
.letter{left:667px;top:130px;width:392px;height:554px}
.letter-watermark{position:absolute;left:79px;top:160px;width:236px;height:236px;border:12px solid var(--watermark);border-radius:50%}
.letter .brand{left:250px;top:29px;width:122px}
.letter-date{position:absolute;left:25px;top:98px;font-size:6.4px;color:var(--ink)}
.recipient{position:absolute;left:25px;top:126px;font-size:6.4px;color:var(--ink);line-height:8.9px}
.recipient strong{color:var(--ink-dark);font-weight:500}
.salutation{position:absolute;left:25px;top:179px;font-size:6.4px;color:var(--ink)}
.letter-body{position:absolute;left:25px;top:197px;width:342px;font-size:6.4px;color:var(--ink);line-height:8.9px}
.letter-body p{text-align:justify;margin-bottom:8.9px}
.signoff{position:absolute;left:25px;top:402px;font-size:6.4px;color:var(--ink)}
.signoff-name{color:var(--ink-dark);font-weight:500}
.signature{display:block;margin:7px 0 8px;width:88px;height:16px;background:linear-gradient(90deg,rgba(11,26,140,.18),rgba(11,26,140,.06))}
.letter .contact{left:25px;top:485px}
.letter .site{left:282px;top:532px}
</style>
</head>
<body>

<!-- Envelope front -->
<section class="sheet envelope-front">
  <div class="brand">
    <span class="brand-ring"></span>
    <span class="brand-name">HARBORLINE</span>
    <span class="brand-sub">REALTY</span>
  </div>
  <div class="contact">
    <div class="contact-row">
      <svg viewBox="0 0 10 10"><path d="M1 3c0-1 1-2 4-2s4 1 4 2v1H7V3H3v1H1zM2 5h6l1 4H1z"/></svg>555.555.5555
      <span class="contact-gap"></span>
      <svg viewBox="0 0 10 10"><path d="M1 2h8v6H1zM1.6 2.6 5 5.4l3.4-2.8"/></svg>office@harborline-realty.com
    </div>
    <div class="contact-row">
      <svg viewBox="0 0 10 10"><path d="M5 0a3.4 3.4 0 0 1 3.4 3.4C8.4 6 5 10 5 10S1.6 6 1.6 3.4A3.4 3.4 0 0 1 5 0zm0 2a1.4 1.4 0 1 0 0 2.8A1.4 1.4 0 0 0 5 2z"/></svg>234 Anywhere, Any City,
    </div>
    <div class="contact-indent">Any Town, US 1234</div>
  </div>
  <svg class="wave" width="474" height="213" viewBox="0 0 474 213">
    <path d="M0 163C100 195 200 200 300 180S430 150 474 150V158C420 160 360 176 290 192S80 195 0 172Z" fill="#5b5b5b"/>
    <path d="M0 180C100 212 220 215 320 192S440 170 474 170V213H0Z" fill="#0b1a8c"/>
  </svg>
  <div class="site">www.harborline-realty.com</div>
</section>

<!-- Envelope back -->
<section class="sheet envelope-back">
  <svg class="flap" width="474" height="80" viewBox="0 0 474 80">
    <path d="M0 0H474L436 66Q428 76 410 76H64Q46 76 38 66Z" fill="#0b1a8c"/>
  </svg>
  <span class="flap-ring"></span>
  <div class="brand">
    <span class="brand-name">HARBORLINE</span>
    <span class="brand-sub">REALTY</span>
  </div>
</section>

<!-- Letterhead -->
<section class="sheet letter">
  <span class="letter-watermark"></span>
  <div class="brand">
    <span class="brand-ring"></span>
    <span class="brand-name">HARBORLINE</span>
    <span class="brand-sub">REALTY</span>
  </div>
  <div class="letter-date">30/20/2016</div>
  <div class="recipient">
    <strong>Mr. Dale Corran</strong><br>123, Street No. 123,<br>City Name<br>Pincode-123456
  </div>
  <div class="salutation">Dear Sir,</div>
  <div class="letter-body">
    <p>Thank you for considering Harborline Realty for your next move. Our team has spent many years helping families and businesses find homes, offices and land that suit their plans and budgets. We study every neighbourhood closely, keep in touch with local owners, and guide each client through viewings, offers, paperwork and closing with patience and care. Whether you are buying your first flat or selling a long held property, we will give you honest advice and steady support at each step of the way.</p>
    <p>Thank you for considering Harborline Realty for your next move. Our team has spent many years helping families and businesses find homes, offices and land that suit their plans and budgets. We study every neighbourhood closely, keep in touch with local owners, and guide each client through viewings, offers, paperwork and closing with patience and care. Whether you are buying your first flat or selling a long held property, we will give you honest advice and steady support at each step of the way.</p>
    <p>Please find enclosed a short summary of current listings in your area along with recent sale prices. We would be glad to arrange a visit at a time that suits you best. Our office is open six days a week.</p>
    <p>Please find enclosed a short summary of current listings in your area along with recent sale prices. We would be glad to arrange a visit at a time that suits you best. Our office is open six days a week.</p>
  </div>
  <div class="signoff">
    <div class="signoff-name">Your Name</div>
    <span class="signature" role="img" aria-label="Handwritten signature"></span>
    <div>CEO &nbsp;|&nbsp; Owner</div>
  </div>
  <div class="contact">
    <div class="contact-row">
      <svg viewBox="0 0 10 10"><path d="M1 3c0-1 1-2 4-2s4 1 4 2v1H7V3H3v1H1zM2 5h6l1 4H1z"/></svg>555.555.5555
      <span class="contact-gap"></span>
      <svg viewBox="0 0 10 10"><path d="M1 2h8v6H1zM1.6 2.6 5 5.4l3.4-2.8"/></svg>office@harborline-realty.com
    </div>
    <div class="contact-row">
      <svg viewBox="0 0 10 10"><path d="M5 0a3.4 3.4 0 0 1 3.4 3.4C8.4 6 5 10 5 10S1.6 6 1.6 3.4A3.4 3.4 0 0 1 5 0zm0 2a1.4 1.4 0 1 0 0 2.8A1.4 1.4 0 0 0 5 2z"/></svg>234 Anywhere, Any City,
    </div>
    <div class="contact-indent">Any Town, US 1234</div>
  </div>
  <svg class="wave" width="392" height="60" viewBox="0 0 392 60">
    <path d="M0 16C80 38 170 44 250 28S350 4 392 4V11C350 12 300 22 240 36S70 44 0 24Z" fill="#5b5b5b"/>
    <path d="M0 30C80 52 190 58 270 40S360 18 392 18V60H0Z" fill="#0b1a8c"/>
  </svg>
  <div class="site">www.harborline-realty.com</div>
</section>

</body>
</html>
```